I would like some help creating my first business cards for my new business, I am a facilitator of a course that I have created. I am currently starting the sales promotion and marketing part of my business and need some help designing the business cards. Something fairly simple would be good, the core theme of my work is in connection of women to themselves and to each other. My initial design is a tree lit up by lights, a very mother earth type of image. This is not my design however so I probably am not legally able to use the design. I don't have a logo. Could you possibly assist with this?

I would really like to have the following details on the business card:
Meg Donlan
0431 582 917
hi.meg.donlan@larkmail.example

And also the image

Target Market(s)

Women who are living in an isolated environment

Industry/Entity Type

Counsellor

Contact Information for Business Card

Meg Donlan
Facilitator
hi.meg.donlan@larkmail.example
0431 582 917

Font styles to use
Other font styles liked:
• Handwriting - Dakota

Colors
e34197
fee18a
3276b5
33a6d7
33b8a4

Requirements
Must have
• 1) My details as above
• 2) a design (picture) that represents the mother earth theme similar to the designs included in the brief
• 3) no copyright attached to the design
• 4) Colours are very important but it is difficult to describe the colour using the colour wheel. Please refer to the example of the tree that I have included in the drop box.
• 5) I must apologise that I forgot to add the business card needs to have the name of the business in gold letters please: Riverbend Circle Gatherings Collective, thank you
Nice to have
• It would be great to use the tree design that I included in the brief, this is my favourite picture but I think it is probably copyrighted. If it's not, that is the one I would like on my business cards please.

```html
<!DOCTYPE html>
<html lang="en">
<head>
<meta charset="utf-8">
<title>Meg Donlan — Business Card</title>
<link rel="stylesheet" href="https://fonts.googleapis.com/css2?family=Great+Vibes&family=Open+Sans:wght@400;700&display=swap">
<style>
  :root {
    --page-bg: #cfe9e0;
    --teal-light: #3dc4b4;
    --teal: #33b8a4;
    --teal-deep: #2aa592;
    --earth: #4e3426;
    --gold: #fee18a;
    --white: #ffffff;
  }
  html, body {
    margin: 0;
    width: 1200px;
    height: 856px;
    overflow: hidden;
    background: var(--page-bg);
  }
  .card {
    position: absolute;
    left: 100px;
    top: 142px;
    width: 1000px;
    height: 572px;
    border-radius: 44px;
    overflow: hidden;
    background: linear-gradient(160deg, var(--teal-light) 0%, var(--teal) 55%, var(--teal-deep) 100%);
    box-shadow: 0 10px 30px rgba(40, 90, 80, 0.18);
    font-family: "Open Sans", sans-serif;
    color: var(--white);
  }
  .tree-art {
    position: absolute;
    left: 20px;
    top: 30px;
    width: 520px;
    height: 520px;
    background:
      radial-gradient(closest-side at 50% 38%, rgba(78, 52, 38, 0.55) 0%, rgba(78, 52, 38, 0.35) 55%, rgba(78, 52, 38, 0) 100%);
  }
  .ground {
    position: absolute;
    left: 0;
    bottom: 0;
    width: 1000px;
    height: 160px;
  }
  .ground path { fill: var(--earth); }
  .identity {
    position: absolute;
    right: 80px;
    top: 36px;
    display: flex;
    align-items: baseline;
    gap: 12px;
  }
  .identity__name {
    font-weight: 700;
    font-size: 28px;
    color: var(--earth);
    margin: 0;
  }
  .identity__role {
    font-size: 18px;
    color: var(--white);
  }
  .business-name {
    position: absolute;
    left: 560px;
    top: 104px;
    width: 400px;
    margin: 0;
    font-family: "Great Vibes", cursive;
    font-weight: 400;
    font-size: 50px;
    line-height: 1.05;
    color: var(--gold);
  }
  .business-name span { display: block; }
  .business-name span:nth-child(2) { padding-left: 36px; }
  .business-name span:nth-child(3) { padding-left: 64px; }
  .contact {
    position: absolute;
    left: 600px;
    top: 320px;
    margin: 0;
    padding: 0;
    list-style: none;
    font-size: 20px;
    line-height: 1.6;
  }
  .contact li { display: flex; align-items: center; gap: 10px; white-space: nowrap; }
  .contact svg { width: 22px; height: 22px; flex: none; }
</style>
</head>
<body>
  <article class="card">
    <div class="tree-art" role="img" aria-label="Silhouette of a tree whose leaves are butterflies, with butterflies drifting away on a faint butterfly pattern"></div>

    <svg class="ground" viewBox="0 0 1000 160" preserveAspectRatio="none" aria-hidden="true">
      <path d="M0 160 L0 120 C120 100 260 92 400 78 C560 62 760 40 1000 22 L1000 160 Z"/>
    </svg>

    <header class="identity">
      <h1 class="identity__name">Meg Donlan</h1>
      <span class="identity__role">Facilitator</span>
    </header>

    <h2 class="business-name">
      <span>Riverbend Circle</span>
      <span>Gatherings</span>
      <span>Collective</span>
    </h2>

    <ul class="contact">
      <li>
        <svg viewBox="0 0 24 24" aria-hidden="true"><circle cx="12" cy="12" r="11" fill="#ffffff"/><path d="M7 10c0-2 2-3 5-3s5 1 5 3l-2 1-1-2h-4l-1 2z M8 12h8l1 4H7z" fill="#33b8a4"/></svg>
        <span>0431 582 917</span>
      </li>
      <li>
        <svg viewBox="0 0 24 24" aria-hidden="true"><circle cx="12" cy="12" r="11" fill="#ffffff"/><rect x="6" y="8" width="12" height="8" rx="1" fill="#33b8a4"/><path d="M6.5 8.5 12 13l5.5-4.5" stroke="#ffffff" stroke-width="1.2" fill="none"/></svg>
        <span>hi.meg.donlan@larkmail.example</span>
      </li>
    </ul>
  </article>
</body>
</html>
```